Business card for a new cabinet shop company named Veloran Cabinets for high end cabinets

Design a business card, thinking dark rich green with colours to speak of high end luxury ie; cream, gold, black possibly

Mitchell Tarrowby
Director Craftsman
Email: info@veloranjoinery-example.com.au
Instagram : @veloran.cabinets

```html
<!DOCTYPE html>
<html lang="en">
<head>
<meta charset="utf-8">
<title>Veloran Cabinets — Business Card</title>
<link href="https://fonts.googleapis.com/css2?family=Arimo:wght@400;700&display=swap" rel="stylesheet">
<style>
  :root {
    --backdrop: #e2e2e2;
    --card-white: #ffffff;
    --ink: #2b2b2b;
    --muted: #6f6f6f;
    --gold: #c9a961;
    --black: #111111;
    --charcoal-top: #353535;
    --charcoal-bottom: #262626;
    --rule: #c8c8c8;
  }
  * { box-sizing: border-box; margin: 0; padding: 0; }
  html, body { width: 1200px; height: 1200px; overflow: hidden; }
  body {
    background: var(--backdrop);
    font-family: "Arimo", Arial, sans-serif;
    position: relative;
  }
  .card {
    position: absolute;
    width: 688px;
    height: 394px;
    border-radius: 22px;
    overflow: hidden;
  }
  .card-front { left: 256px; top: 160px; background: var(--card-white); }
  .card-back {
    left: 256px; top: 650px;
    background: linear-gradient(180deg, var(--charcoal-top), var(--charcoal-bottom));
  }

  .brand {
    position: absolute;
    left: 78px; top: 158px;
    display: flex; align-items: center; gap: 12px;
  }
  .brand-dot { width: 14px; height: 14px; border-radius: 50%; background: var(--gold); }
  .brand-name { color: var(--gold); font-size: 27px; font-weight: 400; letter-spacing: 0.5px; }

  .divider {
    position: absolute; left: 360px; top: 136px;
    width: 1px; height: 101px; background: var(--rule);
  }

  .person { position: absolute; left: 384px; top: 134px; }
  .person-name { color: var(--gold); font-size: 27px; font-weight: 700; line-height: 1; }
  .person-role { color: var(--muted); font-size: 16px; margin-top: 5px; }

  .contacts { position: absolute; left: 384px; top: 198px; list-style: none; }
  .contacts li {
    display: flex; align-items: center; gap: 12px;
    color: var(--ink); font-size: 17px; line-height: 21px;
  }
  .contacts svg { width: 14px; height: 14px; flex: none; }

  .band-black {
    position: absolute; left: 0; bottom: 0;
    width: 400px; height: 16px; background: var(--black);
  }
  .band-gold {
    position: absolute; right: 0; bottom: 0;
    width: 316px; height: 34px; background: var(--gold);
    clip-path: polygon(26px 0, 100% 0, 100% 100%, 0 100%);
    display: flex; align-items: center; justify-content: center;
    padding-left: 26px;
    color: var(--card-white); font-size: 16px;
  }

  .back-brand {
    position: absolute; right: 34px; bottom: 74px;
    color: var(--card-white); font-size: 13px; font-weight: 400; letter-spacing: 0.5px;
  }
</style>
</head>
<body>

<section class="card card-front">
  <div class="brand">
    <span class="brand-dot"></span>
    <span class="brand-name">Veloran Cabinets</span>
  </div>

  <div class="divider"></div>

  <div class="person">
    <p class="person-name">Mitchell Tarrowby</p>
    <p class="person-role">Craftsman</p>
  </div>

  <ul class="contacts">
    <li>
      <svg viewBox="0 0 14 14" aria-hidden="true">
        <rect x="0.5" y="2.5" width="13" height="9" fill="var(--gold)"/>
        <path d="M0.5 2.5 L7 7.5 L13.5 2.5" fill="none" stroke="#fff" stroke-width="1.2"/>
      </svg>
      info@veloranjoinery-example.com.au
    </li>
    <li>
      <svg viewBox="0 0 14 14" aria-hidden="true">
        <circle cx="7" cy="7" r="6.5" fill="var(--gold)"/>
        <path d="M3 4.5 Q5 3.5 6 5.5 T5 9 M8.5 3 Q10 6 9 8.5 T11 11" fill="none" stroke="#fff" stroke-width="1"/>
      </svg>
      @veloran.cabinets
    </li>
  </ul>

  <div class="band-black"></div>
  <div class="band-gold">www.veloranjoinery-example.com.au</div>
</section>

<section class="card card-back" role="img" aria-label="Card reverse with a faint repeating outline pattern over charcoal">
  <span class="back-brand">Veloran Cabinets</span>
</section>

</body>
</html>
```